6 page suburb profile/report for real estate agent to provide to clients

I would like a suburb report to be created in our corporate colours and branding for a local Geelong (Australia) based real estate agent.

The design should be fresh, clean and easy to read, not to cluttered. I dont want a corporate plain boring style.

All content and details are provided and the below link provides a bunch of stock photos that can be used. If you prefer to source some better images from pixmora or framevaultly im happy for them to be ripped and used as low res and if you win the job i will then purchase the images and supply hi res.

I have also included a couple of sample reports produced by other organisations and style/brand guides for our corporation.

The word doc attached has all content to be included and also some notes for your reference. There are a variety of charts to be created (all data provided in word doc), the notes indicating the type/style of chart to be used is a guide only. If you feel you can create a better design/layout using different formats/styles thats fine by me.

If you win the job i will need a further 12 reports produced using the style/format. It will be a case of updating the stats/figures for each report.

If you have any questions regarding the project please dont hesitate to contact me.

6 page document
Page size: A4 Portrait (297mm H x210mm W)
Bleed design off the page
Artwork to setup 100% CMYK
Print ready PDF and live/working files to be supplied
Attached are specs for a variety of programs depending on what you create the job in.
I will require a high res file for printing and also a lower res file suitebale for emailing to clients
Revisions will be required before final files supplied

Stock images
https://www.filecrate-share.example/sh/q7rt2lm9xz4kpw1/BBXQLOWd8RT51Hn4Kc2_Z9pb?dl=0

Target Market(s)

Property owners, property investors, people interested in buying and selling property

Industry/Entity Type

Real Estate Agent

Font styles to use
Serif
Sans Serif
Other font styles liked:
• Source Sans Pro is the corporate font

Colors
0692cd
33a6d7
85cae6
cee9f5
cdddec
85abd2
3176b5
0355a3

Requirements
Must have
• Statistical content provided
• Corporate logo
• Corporate colours - can be creative but dont want a birght happy colour rainbow of colours
Should not have
• Must not represent other real estate agencies corporate colours

```html
<!DOCTYPE html>
<html lang="en">
<head>
<meta charset="utf-8">
<title>Suburb Report – Market Activity</title>
<link href="https://fonts.googleapis.com/css2?family=Source+Sans+3:wght@400;600;700&display=swap" rel="stylesheet">
<style>
:root{
  --stage:#eef3f7;
  --paper:#ffffff;
  --band:#3597d3;
  --heading:#33a6d7;
  --ocean:#0692cd;
  --sky:#85cae6;
  --mist:#cee9f5;
  --panel:#eaf2f9;
  --navy:#0355a3;
  --steel:#3176b5;
  --ink:#1d1d1f;
  --muted:#555;
}
*{margin:0;padding:0;box-sizing:border-box}
html,body{width:1200px;height:836px;overflow:hidden}
body{background:var(--stage);font-family:"Source Sans 3","Source Sans Pro",sans-serif;color:var(--ink);position:relative}
.page{position:absolute;top:72px;width:502px;height:710px;background:var(--paper);overflow:hidden}
.page--left{left:82px}
.page--right{left:608px}
.abs{position:absolute}
.hero{position:absolute;left:0;top:0;width:502px;height:117px}
.hero--living{background:linear-gradient(100deg,#5b4a3f 0%,#8a7563 35%,#d9d2c6 60%,#3b3431 100%)}
.hero--kitchen{background:linear-gradient(100deg,#f1f0ee 0%,#d8d6d3 30%,#2b2b2b 45%,#e9e7e4 60%,#a8a9ab 80%,#f5f5f5 100%)}
.title-band{position:absolute;left:0;top:117px;width:502px;height:34px;background:var(--band);color:#fff;font-size:17.5px;font-weight:600;padding:6px 0 0 35px}
.section-head{position:absolute;left:35px;right:35px;display:flex;align-items:center;gap:6px;color:var(--heading);font-size:14.5px;white-space:nowrap}
.section-head::after{content:"";flex:1;height:1px;background:var(--heading);margin-top:6px}
.stat-total{left:35px;top:196px;font-size:11px;color:var(--muted)}
.stat-total b{font-size:18px;color:var(--ink);font-weight:700;margin-right:2px}
.label-strong{font-size:9.5px;font-weight:700}
.tile{position:absolute;top:222px;height:34px;background:var(--sky);color:#fff}
.tile--pale{background:var(--mist)}
.tile .big{position:absolute;left:6px;top:2px;font-size:17px;font-weight:700}
.tile .small{position:absolute;left:6px;top:21px;font-size:8.5px;opacity:.9}
.tile .inline{font-size:8px;font-weight:400;margin-left:3px}
.tile svg{position:absolute;right:2px;top:2px;width:32px;height:32px}
.price-table{position:absolute;left:35px;top:296px;width:440px;font-size:8.6px}
.price-table .hdr{position:absolute;font-size:9px;color:var(--ink);line-height:1.2}
.price-row{position:absolute;left:0;width:440px;height:15px}
.price-row span{position:absolute;top:0;color:var(--heading)}
.price-row .range{left:0;color:var(--ink)}
.price-row .bar{top:1px;height:12px;background:var(--sky)}
.price-row.total span{font-weight:600}
.subhead{left:35px;top:466px;font-size:9.5px}
.value-box{position:absolute;left:35px;width:171px;height:33px;background:var(--sky);color:#fff}
.value-box .pct{position:absolute;left:6px;top:8px;font-size:14px;font-weight:600}
.value-box svg{position:absolute;left:66px;top:1px;width:32px;height:32px}
.value-box .growth{position:absolute;left:100px;top:7px;font-size:7.6px;line-height:1.3;color:var(--ocean);background:var(--mist);padding:0}
.value-box .growth-wrap{position:absolute;left:98px;top:0;width:73px;height:33px;background:var(--mist)}
.facts{position:absolute;left:40px;font-size:6.6px;line-height:9px;list-style:none}
.facts li::before{content:"";display:inline-block;width:3px;height:3px;border-radius:50%;background:var(--ocean);margin-right:4px;vertical-align:middle}
.facts b{font-weight:700}
.footer-rule{position:absolute;left:35px;width:432px;top:674px;height:1px;background:var(--heading)}
.footnote{position:absolute;right:35px;top:678px;font-size:4.8px;line-height:6px;text-align:right;color:var(--muted)}
.page-no{position:absolute;left:0;width:100%;top:690px;text-align:center;font-size:7.5px;font-weight:700;color:var(--navy)}
.page-no::before,.page-no::after{content:"";display:inline-block;width:19px;height:1px;background:var(--ocean);vertical-align:middle;margin:0 6px}
.rental-head{left:35px;top:210px;font-size:9.5px;font-weight:700}
.rental-copy{position:absolute;left:69px;font-size:7px;line-height:10px}
.rental-copy b{font-weight:700}
.sales-panel{position:absolute;left:0;top:372px;width:502px;height:338px;background:var(--panel)}
.sales-table{position:absolute;left:36px;top:412px;font-size:9px;border-collapse:collapse}
.sales-table th{font-weight:700;text-align:left;padding:0 0 5px;height:18px}
.sales-table td{height:17.6px;padding:0}
</style>
</head>
<body>
<svg width="0" height="0" style="position:absolute">
  <defs>
    <symbol id="icon-house" viewBox="0 0 40 40">
      <path d="M20 6 L36 21 H31 V36 H23 V27 H17 V36 H9 V21 H4 Z" fill="currentColor"/>
    </symbol>
    <symbol id="icon-building" viewBox="0 0 40 40">
      <g fill="none" stroke="currentColor" stroke-width="1.6">
        <rect x="8" y="4" width="24" height="28"/>
        <path d="M13 32 V37 H27 V32"/>
        <path d="M17 32 V37 M23 32 V37"/>
      </g>
      <g fill="none" stroke="currentColor" stroke-width="1.3">
        <rect x="11.5" y="8" width="4" height="4"/><rect x="18" y="8" width="4" height="4"/><rect x="24.5" y="8" width="4" height="4"/>
        <rect x="11.5" y="15" width="4" height="4"/><rect x="18" y="15" width="4" height="4"/><rect x="24.5" y="15" width="4" height="4"/>
        <rect x="11.5" y="22" width="4" height="4"/><rect x="18" y="22" width="4" height="4"/><rect x="24.5" y="22" width="4" height="4"/>
      </g>
    </symbol>
  </defs>
</svg>

<!-- Page 2 -->
<section class="page page--left">
  <div class="hero hero--living" role="img" aria-label="Photograph of a living room with leather sofa and cushions, kitchen bench behind"></div>
  <div class="title-band">Market Activity – past 12 months</div>

  <h2 class="section-head" style="top:171px;font-weight:400">Annual Dwelling Sales</h2>
  <p class="abs stat-total"><b>148</b>properties - 21% lower than one year ago</p>
  <p class="abs label-strong" style="left:271px;top:200px">Auction volume</p>

  <div class="tile" style="left:35px;width:92px">
    <span class="big">76%</span><span class="small">House Sales</span>
    <svg style="color:var(--ocean)"><use href="#icon-house"/></svg>
  </div>
  <div class="tile tile--pale" style="left:139px;width:92px;background:var(--sky)">
    <span class="big">24%</span><span class="small">Unit Sales</span>
    <svg style="color:var(--ocean)"><use href="#icon-building"/></svg>
  </div>
  <div class="tile" style="left:271px;width:96px">
    <span class="big" style="top:6px">32<span class="inline">- 31%</span></span>
    <svg style="color:var(--ocean)"><use href="#icon-house"/></svg>
  </div>
  <div class="tile" style="left:375px;width:92px">
    <span class="big" style="top:6px">2<span class="inline">- 8%</span></span>
    <svg style="color:var(--ocean)"><use href="#icon-building"/></svg>
  </div>

  <h2 class="section-head" style="top:268px;font-weight:400">Sales by Price – Past 12 months</h2>

  <div class="price-table">
    <span class="hdr" style="left:77px;top:13px">Total sales</span>
    <span class="hdr" style="left:150px;top:13px">House</span>
    <span class="hdr" style="left:199px;top:1px">Unit/flat/<br>townhouse</span>
    <span class="hdr" style="left:270px;top:13px">%</span>

    <div class="price-row" style="top:30px"><span class="range">$100k - $199k</span><span style="left:77px">12</span><span style="left:199px">12</span><span class="bar" style="left:270px;width:10.6px"></span><span style="left:389px">8%</span></div>
    <div class="price-row" style="top:45.2px"><span class="range">$200k - $299k</span><span style="left:77px">8</span><span style="left:150px">3</span><span style="left:199px">5</span><span class="bar" style="left:270px;width:7px"></span><span style="left:389px">5%</span></div>
    <div class="price-row" style="top:60.4px"><span class="range">$300k - $399k</span><span style="left:77px">69</span><span style="left:150px">58</span><span style="left:199px">11</span><span class="bar" style="left:270px;width:104px"></span><span style="left:389px">47%</span></div>
    <div class="price-row" style="top:75.6px"><span class="range">$400k - $499k</span><span style="left:77px">36</span><span style="left:150px">32</span><span style="left:199px">4</span><span class="bar" style="left:270px;width:54px"></span><span style="left:389px">24%</span></div>
    <div class="price-row" style="top:90.8px"><span class="range">$500k - $599k</span><span style="left:77px">16</span><span style="left:150px">14</span><span style="left:199px">2</span><span class="bar" style="left:270px;width:25px"></span><span style="left:389px">11%</span></div>
    <div class="price-row" style="top:106px"><span class="range">$600k - $699k</span><span style="left:77px">5</span><span style="left:150px">4</span><span style="left:199px">1</span><span class="bar" style="left:270px;width:5px"></span><span style="left:389px">3%</span></div>
    <div class="price-row" style="top:121.2px"><span class="range">$700k - $799k</span><span style="left:77px">2</span><span style="left:150px">2</span><span class="bar" style="left:270px;width:2px"></span><span style="left:389px">1%</span></div>
    <div class="price-row total" style="top:136.4px"><span style="left:77px">148</span><span style="left:150px">113</span><span style="left:199px">35</span><span style="left:389px">100%</span></div>
  </div>

  <h2 class="section-head" style="top:450px;font-weight:400">Median Values to MAy 2016</h2>
  <p class="abs subhead">Median price change (1yr)</p>

  <div class="value-box" style="top:496px">
    <span class="pct">+1.53%</span>
    <svg style="color:var(--ocean)"><use href="#icon-house"/></svg>
    <div class="growth-wrap"></div>
    <span class="growth">Average annual<br>growth +5.07%</span>
  </div>
  <ul class="facts" style="top:535px">
    <li><b>Median value:</b> $381,250</li>
    <li><b>Average sale price*:</b> $341,722</li>
    <li><b>Avg days on market:</b> 61.52</li>
    <li><b>Vendor discounting:</b> -5.21%</li>
  </ul>

  <div class="value-box" style="top:581px">
    <span class="pct">+28.9%</span>
    <svg style="color:var(--ocean)"><use href="#icon-building"/></svg>
    <div class="growth-wrap"></div>
    <span class="growth">Average annual<br>growth +8.20%</span>
  </div>
  <ul class="facts" style="top:620px">
    <li><b>Median value:</b> $320,000</li>
    <li><b>Average sale price*:</b> $307,458</li>
    <li><b>Avg days on market:</b> 118.57</li>
    <li><b>Vendor discounting:</b> -6.85%</li>
  </ul>

  <p class="abs label-strong" style="left:234px;top:486px">12 Month Median House &amp; Unit Sale Prices</p>
  <svg class="abs" style="left:0;top:0" width="502" height="670" aria-label="Line chart of median house and unit sale prices, May 2015 to May 2016">
    <g font-size="7.5" fill="#1d1d1f" text-anchor="end" font-family="Source Sans 3, sans-serif">
      <text x="268" y="520">$450,000</text><text x="268" y="535">$400,000</text><text x="268" y="550">$350,000</text>
      <text x="268" y="566">$300,000</text><text x="268" y="581">$250,000</text><text x="268" y="596">$200,000</text>
      <text x="268" y="611">$150,000</text><text x="268" y="626">$100,000</text>
    </g>
    <g font-size="7.5" fill="#1d1d1f" font-family="Source Sans 3, sans-serif">
      <text x="395" y="510">House</text><line x1="421" y1="509" x2="431" y2="509" stroke="var(--ocean)"/>
      <text x="440" y="510">Unit</text><line x1="458" y1="509" x2="468" y2="509" stroke="var(--sky)"/>
    </g>
    <polyline fill="none" stroke="var(--sky)" stroke-width="0.9" points="281.6,540 296.8,540 312,542.4 327.2,582.4 342.4,606.4 357.6,585.6 372.8,596 388,568 403.2,560 418.4,617.6 433.6,549.6 448.8,548 464,515.2"/>
    <polyline fill="none" stroke="var(--ocean)" stroke-width="0.9" points="281.6,540 296.8,540 312,544 327.2,526.4 342.4,522.4 357.6,524 372.8,541.6 388,529.6 403.2,518.4 418.4,526.4 433.6,541.6 448.8,531.2 464,546.4"/>
    <g font-size="7.5" fill="#1d1d1f" text-anchor="end" font-family="Source Sans 3, sans-serif">
      <text transform="translate(284.6,628) rotate(-90)">May-16</text>
      <text transform="translate(299.8,628) rotate(-90)">Apr-16</text>
      <text transform="translate(315,628) rotate(-90)">Mar-16</text>
      <text transform="translate(330.2,628) rotate(-90)">Feb-16</text>
      <text transform="translate(345.4,628) rotate(-90)">Jan-16</text>
      <text transform="translate(360.6,628) rotate(-90)">Dec-15</text>
      <text transform="translate(375.8,628) rotate(-90)">Nov-15</text>
      <text transform="translate(391,628) rotate(-90)">Oct-15</text>
      <text transform="translate(406.2,628) rotate(-90)">Sep-15</text>
      <text transform="translate(421.4,628) rotate(-90)">Aug-15</text>
      <text transform="translate(436.6,628) rotate(-90)">Jul-15</text>
      <text transform="translate(451.8,628) rotate(-90)">Jun-15</text>
      <text transform="translate(467,628) rotate(-90)">May-15</text>
    </g>
  </svg>

  <div class="footer-rule"></div>
  <p class="footnote">* based on year to date sales (1/5/15 to 30/4/16)<br># based on year to date sales (1/1/16 to 31/5/16)</p>
  <p class="page-no">2</p>
</section>

<!-- Page 3 -->
<section class="page page--right">
  <div class="hero hero--kitchen" role="img" aria-label="Photograph of a modern white kitchen with stainless steel fridge and wall ovens"></div>
  <div class="title-band">Market Activity – past 12 months</div>

  <h2 class="section-head" style="top:171px;font-weight:400">Median Price – Past 10 years</h2>
  <p class="abs rental-head">Rental Market</p>

  <svg class="abs" style="left:34px;top:237px;width:33px;height:33px;color:var(--ocean)"><use href="#icon-house"/></svg>
  <p class="rental-copy" style="top:240px"><b>Median gross yield:</b> 4.36%<br><b>Median advertised rent:</b> $320pw<br><b>12 month rental change:</b> 1.5%</p>
  <svg class="abs" style="left:34px;top:288px;width:36px;height:36px;color:var(--ocean)"><use href="#icon-building"/></svg>
  <p class="rental-copy" style="top:292px"><b>Median gross yield:</b> 4.06%<br><b>Median advertised rent:</b> $250pw<br><b>12 month rental change:</b> 1.8%</p>

  <svg class="abs" style="left:0;top:0" width="502" height="350" aria-label="Bar chart of median house and unit prices, 2005 to 2015">
    <g font-size="8.5" fill="#1d1d1f" text-anchor="end" font-family="Source Sans 3, sans-serif">
      <text x="258" y="232">$400,000</text><text x="258" y="250">$350,000</text><text x="258" y="268">$300,000</text>
      <text x="258" y="285">$250,000</text><text x="258" y="303">$200,000</text><text x="258" y="321">$150,000</text>
    </g>
    <g font-size="8.5" fill="#1d1d1f" font-family="Source Sans 3, sans-serif">
      <text x="394" y="219">House</text><rect x="422" y="213" width="5" height="5" fill="var(--steel)"/>
      <text x="440" y="219">Unit</text><rect x="460" y="213" width="5" height="5" fill="var(--sky)"/>
    </g>
    <g fill="var(--steel)">
      <rect x="276" y="288" width="12" height="30.4"/><rect x="293.8" y="290.4" width="12" height="28"/>
      <rect x="311.6" y="284.8" width="12" height="33.6"/><rect x="329.4" y="268.8" width="12" height="49.6"/>
      <rect x="347.2" y="264" width="12" height="54.4"/><rect x="365" y="252" width="12" height="66.4"/>
      <rect x="382.8" y="252" width="12" height="66.4"/><rect x="400.6" y="255.2" width="12" height="63.2"/>
      <rect x="418.4" y="239.2" width="12" height="79.2"/><rect x="436.2" y="237.6" width="12" height="80.8"/>
      <rect x="454" y="229.6" width="12" height="88.8"/>
    </g>
    <g fill="var(--sky)">
      <rect x="278" y="300.8" width="8" height="17.6"/><rect x="295.8" y="293.6" width="8" height="24.8"/>
      <rect x="315.6" y="280.8" width="8" height="37.6"/><rect x="331.4" y="270.4" width="10" height="48"/>
      <rect x="349.2" y="272" width="8" height="46.4"/><rect x="367" y="272" width="8" height="46.4"/>
      <rect x="384.8" y="257.6" width="8" height="60.8"/><rect x="402.6" y="282.4" width="8" height="36"/>
      <rect x="420.4" y="257.6" width="8" height="60.8"/><rect x="438.2" y="268.8" width="8" height="49.6"/>
      <rect x="456" y="255.2" width="10" height="63.2"/>
    </g>
    <g font-size="8.5" fill="#1d1d1f" text-anchor="end" font-family="Source Sans 3, sans-serif">
      <text transform="translate(285,322) rotate(-90)">2005</text><text transform="translate(302.8,322) rotate(-90)">2006</text>
      <text transform="translate(320.6,322) rotate(-90)">2007</text><text transform="translate(338.4,322) rotate(-90)">2008</text>
      <text transform="translate(356.2,322) rotate(-90)">2009</text><text transform="translate(374,322) rotate(-90)">2010</text>
      <text transform="translate(391.8,322) rotate(-90)">2011</text><text transform="translate(409.6,322) rotate(-90)">2012</text>
      <text transform="translate(427.4,322) rotate(-90)">2013</text><text transform="translate(445.2,322) rotate(-90)">2014</text>
      <text transform="translate(463,322) rotate(-90)">2015</text>
    </g>
  </svg>

  <div class="sales-panel"></div>
  <h2 class="section-head" style="top:382px;font-weight:400">Top 10 sales#</h2>

  <table class="sales-table">
    <colgroup><col style="width:25px"><col style="width:121px"><col style="width:38px"><col style="width:43px"><col style="width:38px"><col style="width:65px"><col style="width:56px"><col style="width:60px"></colgroup>
    <thead><tr><th>No</th><th>Address</th><th>Bed</th><th>Bath</th><th>Car</th><th>Sale Date</th><th>Land Size</th><th>Sale Price</th></tr></thead>
    <tbody>
      <tr><td><b>1</b></td><td>21 Silverleaf Drive</td><td>4</td><td>2</td><td>2</td><td>29/03/2016</td><td>675</td><td>$750,000</td></tr>
      <tr><td><b>2</b></td><td>1-3/352 Chapel Row</td><td>4</td><td>3</td><td>3</td><td>01/03/2016</td><td>668</td><td>$604,000</td></tr>
      <tr><td><b>3</b></td><td>16 Marlow Close</td><td>4</td><td>2</td><td>2</td><td>13/02/2016</td><td>756</td><td>$600,000</td></tr>
      <tr><td><b>4</b></td><td>24 Bellbird Street</td><td>3</td><td>2</td><td>2</td><td>01/03/2016</td><td>766</td><td>$600,000</td></tr>
      <tr><td><b>5</b></td><td>24b Harbourview Parade</td><td>4</td><td>3</td><td>1</td><td>25/02/2016</td><td>337</td><td>$530,000</td></tr>
      <tr><td><b>6</b></td><td>2-4 Dorset Street</td><td>4</td><td>3</td><td>3</td><td>05/02/2016</td><td>692</td><td>$520,000</td></tr>
      <tr><td><b>7</b></td><td>62 Dunmore Avenue</td><td>4</td><td>2</td><td>2</td><td>10/02/2016</td><td>672</td><td>$518,000</td></tr>
      <tr><td><b>8</b></td><td>9a Glenfield Street</td><td>3</td><td>2</td><td>1</td><td>04/02/2016</td><td>319</td><td>$495,000</td></tr>
      <tr><td><b>9</b></td><td>9b Glenfield Street</td><td>3</td><td>2</td><td>1</td><td>23/01/2016</td><td>319</td><td>$495,000</td></tr>
      <tr><td><b>10</b></td><td>38 Ballard Road</td><td>3</td><td>2</td><td>2</td><td>10/02/2016</td><td>261</td><td>$480,000</td></tr>
    </tbody>
  </table>

  <div class="footer-rule"></div>
  <p class="footnote">* based on year to date sales (1/5/15 to 30/4/16)<br># based on year to date sales (1/1/16 to 31/5/16)</p>
  <p class="page-no">3</p>
</section>
</body>
</html>
```